Wordpress Design Project for Employee Communications Site

We need a Wordpress design for a company that strategizes on and produces materials for employee communications. Improving employee communications at all levels of an organization can help improve overall company performance and results. The site needs to look very clean and professional; we're not afraid of white space. We like the functionality that Wordpress provides; however, we only want one "true" blog page; the other pages should give the impression of a more "static" web site - particularly the home page. I have a logo that I can provide.

I have added these comments to the discussion page:
Great question - thank you for asking it. I’ve done more research

I like the very clean and monochromatic looks to many of these. I don’t have to have monochromatic, but I do like minimal colors. Simple, clean, organized. The home page should “fit” almost entirely without scrolling. I do like fat footers that you can scroll down to. I don’t want a colored background, but any that I’ve chosen with colored backgrounds could be switched to a white background.

http://www.mirabelquennet.example/
http://pondraft.example/
http://v1.samplumworth.example/
http://howdythegoat.example/
http://stayingbrisk.example/
http://www.interiors.kelmun.example/
http://trelvmasters.example/

These last two are more corporate sites. The first one is from a well-respected consultant in my area who does a lot of what I do. And I think Harwenby does a nice job with their site. So, I want to marry the look I like with getting the content job done.

http://www.messagefuelbox.example/
http://www.harwenby.example/view/en_US/us/index.htm

Target Market(s)

Target market is mid- to large-sized companies. More than 500 employees.

Industry/Entity Type

Communications

Requirements
Must have
• Need an impactful home page. There should be a "blog" page; contact us; services; about. For starters, at least. I want fonts to be very readable - that is, either quite dark gray or black.
Nice to have
• I am loathe to include a picture of myself, but I do want some images that say, "professional" and "expert" in communications.
Should not have
• I don't want a hits counter :) (I know no one would do that!).

```html
<!DOCTYPE html>
<html lang="en">
<head>
<meta charset="utf-8">
<title>Meridale Communications Group</title>
<link rel="stylesheet" href="https://fonts.googleapis.com/css2?family=Oswald:wght@400&family=Noto+Sans:wght@400;700&family=Arimo&display=swap">
<style>
  :root {
    --lime: #bed639;
    --sky: #6cc4ea;
    --ink: #3a3a3a;
    --text: #2e2e2e;
    --muted: #8c8c8c;
    --rule: #dcdcdc;
    --paper: #ffffff;
  }
  * { margin: 0; padding: 0; box-sizing: border-box; }
  html, body { width: 1200px; height: 987px; overflow: hidden; background: var(--paper); }
  body { position: relative; font-family: "Noto Sans", sans-serif; color: var(--text); }

  .top-band { position: absolute; left: 0; top: 0; width: 1200px; height: 11px; background: var(--lime); }

  .brand { position: absolute; left: 216px; top: 58px; display: flex; align-items: center; gap: 12px; }
  .brand-dot { width: 34px; height: 34px; border-radius: 50%; background: var(--sky); }
  .brand-name { font-family: "Oswald", sans-serif; font-weight: 400; font-size: 32px; color: var(--lime); letter-spacing: .5px; }

  .main-nav { position: absolute; top: 143px; left: 0; width: 1200px; }
  .main-nav a { position: absolute; font-family: "Oswald", sans-serif; font-size: 18px; color: var(--ink); text-decoration: none; }
  .nav-rule { position: absolute; left: 100px; top: 173px; width: 1000px; height: 6px;
    background: radial-gradient(ellipse at center, rgba(0,0,0,.18) 0%, rgba(0,0,0,0) 70%); }

  .slider-shadow { position: absolute; left: 210px; top: 470px; width: 800px; height: 40px;
    background: radial-gradient(ellipse at center top, rgba(0,0,0,.22) 0%, rgba(0,0,0,0) 65%); }
  .slide { position: absolute; left: 297px; top: 181px; width: 627px; height: 308px; border: 1px solid #b9b9b9;
    background: linear-gradient(135deg, #d9dde2 0%, #c8d3df 35%, #9fb7d6 55%, #e4e8ec 80%, #cfd6de 100%); }
  .slide-caption { position: absolute; left: 0; top: 98px; width: 240px; height: 88px; background: var(--lime);
    border-radius: 0 10px 10px 0; padding: 5px 11px; }
  .slide-caption h2 { font-family: "Oswald", sans-serif; font-weight: 400; font-size: 21px; color: #fff; line-height: 26px; }
  .slide-caption p { font-size: 12px; line-height: 15.5px; color: #2e3a10; text-align: justify; }
  .slider-arrow { position: absolute; top: 304px; }
  .slider-dots { position: absolute; left: 580px; top: 497px; display: flex; gap: 6px; }
  .slider-dots span { width: 13px; height: 13px; border-radius: 50%; background: #9a9a9a; }
  .slider-dots span.is-active { background: var(--sky); }

  .teaser { position: absolute; width: 227px; }
  .teaser h3 { font-family: "Oswald", sans-serif; font-weight: 400; font-size: 20px; color: var(--ink); line-height: 24px; margin-bottom: 8px; letter-spacing: -.2px; }
  .teaser p { font-size: 12.4px; line-height: 15.6px; text-align: justify; color: var(--text); hyphens: auto; }
  .read-more { display: flex; align-items: center; gap: 6px; margin-top: 12px; font-size: 12px; font-weight: 700; color: #222; }
  .read-more i { width: 16px; height: 13px; border-radius: 50%; background: var(--sky); }
  .attribution { margin-top: 7px; text-align: right; font-size: 12px; font-weight: 700; line-height: 14.5px; color: var(--ink); }
  .col-rule { position: absolute; width: 1px; background: linear-gradient(to bottom, rgba(0,0,0,0), var(--rule), rgba(0,0,0,0)); }

  .footer-rule { position: absolute; left: 85px; top: 924px; width: 1000px; height: 8px;
    background: radial-gradient(ellipse at center, rgba(0,0,0,.2) 0%, rgba(0,0,0,0) 70%); }
  .footer-brand { position: absolute; left: 201px; top: 944px; display: flex; align-items: center; gap: 6px; }
  .footer-brand .brand-dot { width: 18px; height: 18px; background: #a9a9a9; }
  .footer-brand .brand-name { font-size: 15px; color: #9a9a9a; }
  .footer-nav { position: absolute; left: 424px; top: 938px; font-family: "Arimo", sans-serif; font-size: 13px; color: #333; word-spacing: 2px; }
  .footer-nav a { color: #333; text-decoration: none; }
  .footer-nav .sep { margin: 0 15px; }
  .copyright { position: absolute; left: 441px; top: 968px; font-family: "Arimo", sans-serif; font-size: 11px; color: #333; }
  .social { position: absolute; left: 903px; top: 936px; display: flex; }
  .social span { width: 40px; height: 40px; border-radius: 50%; }
  .social .one { background: var(--sky); }
  .social .two { background: var(--lime); margin-left: -10px; }
</style>
</head>
<body>
  <div class="top-band"></div>

  <header>
    <div class="brand"><span class="brand-dot"></span><span class="brand-name">Meridale Communications Group</span></div>
    <nav class="main-nav">
      <a style="left:359px">Home</a>
      <a style="left:459px">About</a>
      <a style="left:566px">Services</a>
      <a style="left:693px">Blog</a>
      <a style="left:787px">Contact us</a>
    </nav>
    <div class="nav-rule"></div>
  </header>

  <section class="slider">
    <div class="slider-shadow"></div>
    <div class="slide" role="img" aria-label="Photo of colleagues reviewing documents together at a meeting table">
      <div class="slide-caption">
        <h2>Effective Communication</h2>
        <p>Effective communication in the workplace is the backbone of any business.</p>
      </div>
    </div>
    <svg class="slider-arrow" style="left:235px" width="30" height="32" viewBox="0 0 30 32"><polygon points="30,0 14,16 30,32 16,32 0,16 16,0" fill="var(--lime)"/></svg>
    <svg class="slider-arrow" style="left:945px" width="30" height="32" viewBox="0 0 30 32"><polygon points="0,0 16,16 0,32 14,32 30,16 14,0" fill="var(--lime)"/></svg>
    <div class="slider-dots"><span class="is-active"></span><span></span><span></span><span></span></div>
  </section>

  <main>
    <article class="teaser" style="left:209px;top:541px">
      <h3>External Communication</h3>
      <p>Effective communication in the work&shy;place is the backbone of any business. Without it, you could miss out on important opportunities, waste time and cause your employees and custom&shy;ers to become frustrated.</p>
      <div class="read-more"><i></i>Read More</div>
    </article>
    <div class="col-rule" style="left:461px;top:560px;height:110px"></div>
    <article class="teaser" style="left:488px;top:541px">
      <h3>Business Growth</h3>
      <p>Effective communication in the work&shy;place is the backbone of any business. Without it, you could miss out on important opportunities, waste time and cause your employees and custom&shy;ers to become frustrated.</p>
      <div class="read-more"><i></i>Read More</div>
    </article>
    <div class="col-rule" style="left:737px;top:560px;height:110px"></div>
    <article class="teaser" style="left:764px;top:541px">
      <h3>Internal Communication</h3>
      <p>Effective communication in the work&shy;place is the backbone of any business. Without it, you could miss out on important opportunities, waste time and cause your employees and custom&shy;ers to become frustrated.</p>
      <div class="read-more"><i></i>Read More</div>
    </article>

    <article class="teaser" style="left:209px;top:737px">
      <h3>What Customers are Saying...</h3>
      <p>MCG is a great benchmarking tool."The MCG channels offer a very effective way to communicate with geographi&shy;cally distributed stores and in a retail environment."</p>
      <div class="attribution">Lorna Vesselby<br>Internal Communications<br>Manager</div>
    </article>
    <div class="col-rule" style="left:461px;top:760px;height:110px"></div>
    <article class="teaser" style="left:488px;top:737px">
      <h3>Internal Social Media</h3>
      <p>MCG is a great benchmarking tool."The MCG channels offer a very effective way to communicate with geographi&shy;cally distributed stores and in a retail environment."</p>
      <div class="attribution">Specifically for employee<br>communication</div>
    </article>
    <div class="col-rule" style="left:740px;top:760px;height:110px"></div>
    <article class="teaser" style="left:765px;top:737px">
      <h3>Business Growth</h3>
      <p>MCG is a great benchmarking tool."The MCG channels offer a very effective way to communicate with geographi&shy;cally distributed stores and in a retail environment."</p>
      <div class="attribution">Specifically for employee<br>communication</div>
    </article>
  </main>

  <footer>
    <div class="footer-rule"></div>
    <div class="footer-brand"><span class="brand-dot"></span><span class="brand-name">Meridale Communications Group</span></div>
    <nav class="footer-nav">
      <a>Home</a><span class="sep">|</span><a>About</a><span class="sep">|</span><a>Services</a><span class="sep">|</span><a>Blog</a><span class="sep">|</span><a>Contact Us</a>
    </nav>
    <p class="copyright">All rights reserved. © Meridale Communications Group 2008</p>
    <div class="social"><span class="one"></span><span class="two"></span></div>
  </footer>
</body>
</html>
```